Vantiqo custom business card design

Need a authentic, innovative business card design for a new mobile app business. I am uploading a few screen images from our app for you to view. I would like app design theme to match business card design. I can also send logo images.

```html
<!DOCTYPE html>
<html lang="en">
<head>
<meta charset="UTF-8">
<title>Vantiqo Business Card</title>
<link rel="stylesheet" href="https://fonts.googleapis.com/css2?family=Work+Sans:wght@400;500;800&display=swap">
<style>
  :root {
    --stage: #1e1e1e;
    --card: #262626;
    --card-edge: #303030;
    --ink: #f4f4f4;
    --ink-soft: #d9d9d9;
    --accent: #6b35a8;
    --mark-light: #f0f0f0;
    --mark-dark: #3a3a3a;
  }
  * { margin: 0; padding: 0; box-sizing: border-box; }
  html, body {
    width: 1200px; height: 900px; overflow: hidden;
    background: var(--stage);
    font-family: "Work Sans", Arial, sans-serif;
  }
  .canvas {
    position: relative; width: 1200px; height: 900px;
  }
  .card {
    position: absolute; left: 270px; width: 660px; height: 378px;
    background: var(--card);
    border: 1px solid var(--card-edge);
    box-shadow: 0 18px 40px rgba(0,0,0,.55);
  }
  .card--front { top: 50px; }
  .card--back { top: 468px; }

  /* front */
  .front-mark {
    position: absolute; left: 50%; top: 78px; transform: translateX(-50%);
    display: flex; flex-direction: column; align-items: center; gap: 18px;
  }
  .front-mark__dot {
    width: 140px; height: 140px; border-radius: 50%;
    background: linear-gradient(110deg, var(--mark-dark), var(--mark-light));
  }
  .front-mark__name {
    font-weight: 800; font-size: 44px; color: var(--ink-soft); letter-spacing: .5px;
  }

  /* back */
  .brand {
    position: absolute; left: 40px; top: 30px;
    font-weight: 800; font-size: 56px; color: var(--ink); letter-spacing: .5px;
  }
  .person { position: absolute; left: 42px; top: 126px; }
  .person__name {
    font-weight: 500; font-size: 27px; color: var(--accent); text-transform: uppercase; letter-spacing: 1px;
  }
  .person__role { font-size: 19px; color: var(--ink-soft); margin-top: 2px; }
  .address {
    position: absolute; left: 42px; top: 196px;
    font-size: 20px; line-height: 28px; color: var(--ink-soft); letter-spacing: .5px;
  }
  .contacts {
    position: absolute; left: 42px; top: 262px; list-style: none;
    font-size: 20px; line-height: 27px; color: var(--ink-soft); letter-spacing: .5px;
  }
  .contacts li { display: flex; align-items: center; gap: 12px; }
  .contacts svg { width: 15px; height: 15px; flex: none; }
  .back-mark {
    position: absolute; right: 40px; top: 36px;
    width: 306px; height: 306px; border-radius: 50%;
    background: linear-gradient(110deg, var(--mark-dark) 10%, var(--mark-light) 85%);
  }
</style>
</head>
<body>
<main class="canvas">
  <section class="card card--front">
    <div class="front-mark">
      <div class="front-mark__dot"></div>
      <div class="front-mark__name">Vantiqo</div>
    </div>
  </section>

  <section class="card card--back">
    <h1 class="brand">Vantiqo</h1>
    <div class="person">
      <div class="person__name">Dana Whitfield</div>
      <div class="person__role">Director</div>
    </div>
    <address class="address" style="font-style:normal">
      1427 Harbor Lane<br>Coral Bay, FL 32980
    </address>
    <ul class="contacts">
      <li>
        <svg viewBox="0 0 16 16" fill="none" stroke="#6b35a8" stroke-width="1.4"><rect x="4" y="1" width="8" height="14" rx="1.5"/><line x1="7" y1="12.5" x2="9" y2="12.5"/></svg>
        (555) 014-2273
      </li>
      <li>
        <svg viewBox="0 0 16 16" fill="#6b35a8"><path d="M4 1l2.5 3-1.5 2c1 2 2.5 3.5 4.5 4.5l2-1.5 3 2.5-1.5 2.5C7 15 1 9 1.5 3.5z"/></svg>
        (555) 018-6640
      </li>
      <li>
        <svg viewBox="0 0 16 16" fill="none" stroke="#6b35a8" stroke-width="1.4"><rect x="1.5" y="3.5" width="13" height="9"/><path d="M1.5 3.5L8 9l6.5-5.5"/></svg>
        info@Vantiqo.com
      </li>
      <li>
        <svg viewBox="0 0 16 16" fill="none" stroke="#6b35a8" stroke-width="1.2"><circle cx="8" cy="8" r="6.5"/><ellipse cx="8" cy="8" rx="3" ry="6.5"/><line x1="1.5" y1="8" x2="14.5" y2="8"/></svg>
        www.Vantiqo.com
      </li>
    </ul>
    <div class="back-mark"></div>
  </section>
</main>
</body>
</html>
```